BrivoTerna. Lantern of the Steady Harvest. Business card

Professional business card for BrivoTerna (Lantern of the Steady Harvest)
My rationale: Strategy-> Execution-> Results-> Value that lead to the BrivoTerna name: We put the Lantern of the Steady Harvest.
We deliver value to our customers helping them at defining a good strategy (cyan arrow). 90% of well formulated strategies fail due to poor execution so we also consider strategical execution very important (green arrow). Due to the execution we obtain the results (blue arrow). Finally, the results provide feedback to redefine strategy, and the new strategy has to be executed and new results obtained providing new feedback and on and on. It's like a wheel that finally, must create corporate value: value for shareholders, staholders, employees, providers...-

Target Market(s)

CEOs and steering comitees , invewrnent funds

Industry/Entity Type

Business Consultant

Contact Information for Business Card

Teodoro Vinsquel
CEO & Founder
teodoro.vinsquel@brivoterna-example.com
Mobile: +34 655.803.912
www.brivoterna-example.com

Colors

Designer to choose colors to be used in the design.

Requirements
Nice to have
• Nice to hace the words: Strategy, execution, results
• Nice to vave the claim: Lantern of the Steady Harvest
• The three colors should be shown:
• cyan for STRATEGY
• green for EXECUTION
• blue for RESULTS
Should not have
• Complete black background

```html
<!DOCTYPE html>
<html lang="en">
<head>
<meta charset="utf-8">
<title>BrivoTerna – Business Card</title>
<link href="https://fonts.googleapis.com/css2?family=Lato:wght@400;700&display=swap" rel="stylesheet">
<style>
  :root {
    --backdrop: #5c5c5c;
    --card: #111114;
    --card-edge: #1f3a9e;
    --brand-blue: #2b4aa8;
    --info-cyan: #2aa6d8;
    --icon-green: #9acd32;
    --pattern-dark: #1a1a1d;
    --pattern-light: #3a3a3e;
  }
  * { margin: 0; padding: 0; box-sizing: border-box; }
  html, body {
    width: 1200px; height: 900px; overflow: hidden;
    background: var(--backdrop);
    font-family: "Lato", Arial, sans-serif;
  }
  .sheet {
    width: 1200px; height: 900px;
    display: flex; align-items: center; justify-content: center; gap: 40px;
  }
  .card {
    position: relative;
    width: 540px; height: 310px;
    background: var(--card);
    border: 2px solid var(--card-edge);
    box-shadow: 0 14px 30px rgba(0,0,0,.45);
    overflow: hidden;
  }
  /* front */
  .brand {
    position: absolute; left: 34px; top: 0; bottom: 0; width: 200px;
    display: flex; align-items: center; gap: 10px;
  }
  .brand-dot { width: 18px; height: 18px; border-radius: 50%; background: var(--brand-blue); flex: none; }
  .brand-name { color: var(--brand-blue); font-weight: 700; font-size: 30px; letter-spacing: -.5px; }
  .divider {
    position: absolute; left: 248px; top: 46px; bottom: 46px;
    width: 1px; background: var(--card-edge);
  }
  .details { position: absolute; left: 270px; top: 52px; right: 18px; }
  .person-name { color: var(--brand-blue); font-weight: 700; font-size: 25px; line-height: 1.1; }
  .person-role { color: var(--info-cyan); font-size: 13px; margin-top: 4px; }
  .address { color: var(--info-cyan); font-size: 12.5px; line-height: 1.35; margin-top: 14px; }
  .contacts { list-style: none; margin-top: 12px; }
  .contacts li {
    display: flex; align-items: center; gap: 8px;
    color: var(--info-cyan); font-size: 12px; line-height: 1.55; white-space: nowrap;
  }
  .contacts svg { width: 12px; height: 12px; flex: none; }
  /* back */
  .pattern-field {
    position: absolute; inset: 0;
    background: linear-gradient(135deg, var(--pattern-light) 0%, var(--pattern-dark) 45%, var(--pattern-light) 100%);
  }
  .back-mark {
    position: absolute; left: 0; right: 0; top: 205px;
    display: flex; align-items: center; justify-content: center; gap: 8px;
  }
  .back-mark .brand-dot { width: 12px; height: 12px; }
  .back-mark .brand-name { font-size: 20px; }
</style>
</head>
<body>
<main class="sheet">
  <section class="card card-front" aria-label="Business card front">
    <div class="brand">
      <span class="brand-dot"></span>
      <span class="brand-name">BrivoTerna</span>
    </div>
    <div class="divider"></div>
    <div class="details">
      <h1 class="person-name">Teodoro Vinsquel</h1>
      <p class="person-role">Founder &amp; CEO</p>
      <p class="address">Calle Orvento 58,<br>Valdemira, 08140 España</p>
      <ul class="contacts">
        <li>
          <svg viewBox="0 0 12 12"><path d="M3 1l2 2.5-1 1.2c.6 1.3 1.6 2.3 2.9 2.9L8.1 6.6 10.6 8.6 9.6 10.6C5.4 10.3 1.7 6.6 1.4 2.4z" fill="var(--icon-green)"/></svg>
          +34 655.803.912
        </li>
        <li>
          <svg viewBox="0 0 12 12"><rect x="1" y="2.5" width="10" height="7" fill="var(--icon-green)"/><path d="M1 2.5l5 4 5-4" stroke="var(--card)" stroke-width="1" fill="none"/></svg>
          teodoro.vinsquel@brivoterna-example.com
        </li>
        <li>
          <svg viewBox="0 0 12 12"><circle cx="6" cy="6" r="5" fill="var(--icon-green)"/><path d="M1 6h10M6 1c-2 2.7-2 7.3 0 10M6 1c2 2.7 2 7.3 0 10" stroke="var(--card)" stroke-width=".8" fill="none"/></svg>
          www.brivoterna-example.com
        </li>
      </ul>
    </div>
  </section>

  <section class="card card-back" aria-label="Business card back">
    <div class="pattern-field" role="img" aria-label="Repeating tonal pattern of dark glossy brand motifs"></div>
    <div class="back-mark">
      <span class="brand-dot"></span>
      <span class="brand-name">BrivoTerna</span>
    </div>
  </section>
</main>
</body>
</html>
```